TA BRAMLEY BUSINESS CARD DESIGN PROJECT

We need to utilize our logo that was expertly created on PixelHarbor and now need to match this with a business card design.

```html
<!DOCTYPE html>
<html lang="en">
<head>
<meta charset="UTF-8">
<title>TA BRAMLEY Business Card</title>
<link href="https://fonts.googleapis.com/css2?family=Open+Sans:wght@400;600;700&display=swap" rel="stylesheet">
<style>
  :root {
    --brand-blue: #1158a8;
    --card-black: #171717;
    --paper-white: #ffffff;
    --page-bg: #e9eaec;
    --text-light: #f2f2f2;
  }
  * { margin: 0; padding: 0; box-sizing: border-box; }
  html, body {
    width: 1200px; height: 900px; overflow: hidden;
    background: var(--page-bg);
    font-family: "Open Sans", Arial, sans-serif;
  }
  .sheet {
    width: 1200px; height: 900px;
    display: flex; flex-direction: column; align-items: center; justify-content: center;
    gap: 40px;
  }
  .card {
    position: relative;
    width: 630px; height: 360px;
    border-radius: 22px;
    overflow: hidden;
    box-shadow: 0 10px 28px rgba(0,0,0,0.18);
  }
  .card-front {
    background: var(--brand-blue);
    display: flex; align-items: center; justify-content: center;
  }
  .brand-name {
    font-weight: 700;
    letter-spacing: 0.14em;
    white-space: nowrap;
  }
  .card-front .brand-name {
    color: var(--paper-white);
    font-size: 56px;
  }
  .card-back { background: var(--card-black); }
  .back-shape { position: absolute; inset: 0; }
  .back-brand {
    position: absolute;
    left: 345px; top: 150px; width: 260px;
    text-align: center;
  }
  .back-brand .brand-name {
    color: var(--brand-blue);
    font-size: 27px;
  }
  .contact {
    position: absolute;
    left: 40px; bottom: 38px;
    color: var(--text-light);
    font-size: 15px;
    line-height: 1.4;
  }
  .contact-name {
    color: var(--brand-blue);
    font-weight: 700;
    font-size: 24px;
    line-height: 1.1;
    letter-spacing: 0.01em;
  }
  .contact-title { margin-bottom: 16px; }
  .contact-address { margin-bottom: 14px; }
  .contact-line { display: flex; align-items: center; gap: 8px; }
  .contact-line svg { width: 13px; height: 13px; flex: none; }
</style>
</head>
<body>
<main class="sheet">
  <section class="card card-front" aria-label="Card front">
    <span class="brand-name">TA BRAMLEY</span>
  </section>

  <section class="card card-back" aria-label="Card back">
    <svg class="back-shape" viewBox="0 0 630 360" aria-hidden="true">
      <path d="M 470 -120 A 270 270 0 0 0 300 360 L 630 360 L 630 0 Z" fill="none"/>
      <circle cx="560" cy="115" r="260" fill="var(--paper-white)"/>
      <path d="M 330 -20 A 260 260 0 0 0 430 345" fill="none" stroke="var(--brand-blue)" stroke-width="7"/>
      <path d="M 318 60 A 262 262 0 0 0 470 365" fill="none" stroke="var(--brand-blue)" stroke-width="3"/>
    </svg>

    <div class="back-brand">
      <span class="brand-name">TA BRAMLEY</span>
    </div>

    <div class="contact">
      <p class="contact-name">OWEN HARTLEY</p>
      <p class="contact-title">Managing Director</p>
      <p class="contact-address">Your address, City<br>State, Zip 1234</p>
      <p class="contact-line">
        <svg viewBox="0 0 16 16"><path d="M3 1h3l1.5 4-2 1.5a9 9 0 0 0 4 4L11 8.5l4 1.5v3a2 2 0 0 1-2 2A13 13 0 0 1 1 3a2 2 0 0 1 2-2z" fill="var(--brand-blue)"/></svg>
        123 456 789
      </p>
      <p class="contact-line">
        <svg viewBox="0 0 16 16"><rect x="1" y="3" width="14" height="10" rx="1" fill="var(--brand-blue)"/><path d="M1.5 4l6.5 5 6.5-5" fill="none" stroke="var(--card-black)" stroke-width="1.3"/></svg>
        info@yourmail.com
      </p>
      <p class="contact-line">
        <svg viewBox="0 0 16 16"><circle cx="8" cy="8" r="7" fill="var(--brand-blue)"/><path d="M1 8h14M8 1c-3 3-3 11 0 14M8 1c3 3 3 11 0 14" fill="none" stroke="var(--card-black)" stroke-width="1"/></svg>
        www.yourwebsite.com
      </p>
    </div>
  </section>
</main>
</body>
</html>
```